IT company developing solutions for air cargo industry is looking for a new website

We are a professional IT company developing solutions for air cargo industry worldwide.

We are looking to update and completely redesign our current webpages: https://www.brisklane.cz/

What we like about our current pages are the animated graphics on the home page. These could stay, but not a must.

The design of the new pages should be very modern, clean, unique, creative, professional, and to make a statement. We are looking for animated graphics, cool and interesting interactions, cascading layers, etc.

Our company logo is yellow, gray and black. You don’t necessarily have to stick to this colour scheme, however the corporate colors should work well with the overal design of the web pages.
Dark mode pages are also an option.

The scope of the project would include creating a:

• Header
• Footer
• Landing page
• Navigation bar (8 tabs)
• Subpages (10)

In the first stage we are looking only for the header / footer / landing page with navigaton bar / Solutions page design.
As a second round, finalists might be asked to submit another section of the website to see their consistency in terms of the look and feel proposed for the Homepage and Solutions’ pages.
The winning designer will then complete the rest of the pages.

Attached you will find a brief for the first scope of the project. Please read the note section on slide nr. 3 carefully to understand, what we exactly are looking for to achieve.

Industry/Entity Type

Aviation

Number of Pages Required

1 page

Requirements
Must have
• See brief
Nice to have
• See brief
Should not have
• See brief

```html
<!DOCTYPE html>
<html lang="en">
<head>
<meta charset="utf-8">
<title>Brisklane – Air Cargo IT Solutions</title>
<link href="https://fonts.googleapis.com/css2?family=Figtree:wght@400;500;700;800&family=Overpass:wght@400;500&display=swap" rel="stylesheet">
<style>
  :root {
    --gold: #fec820;
    --black: #000;
    --ink: #111;
    --white: #fff;
    --muted: #1a1a1a;
  }
  * { margin: 0; padding: 0; box-sizing: border-box; }
  html, body { width: 998px; height: 1200px; overflow: hidden; background: var(--black); }
  body { position: relative; font-family: "Figtree", sans-serif; color: var(--white); }

  .promo-bar {
    position: absolute; top: 0; left: 0; width: 998px; height: 33px;
    background: var(--gold); color: var(--ink);
    font-family: "Overpass", sans-serif; font-size: 11px;
    display: flex; align-items: center; justify-content: center;
  }

  .brand {
    display: flex; align-items: center; gap: 8px;
    font-family: "Figtree", sans-serif; font-weight: 500; color: var(--white);
  }
  .brand-mark { background: var(--gold); display: block; }

  .site-header .brand { position: absolute; left: 80px; top: 52px; font-size: 28px; }
  .site-header .brand-mark { width: 30px; height: 30px; }

  .main-nav {
    position: absolute; top: 67px; left: 384px; display: flex; gap: 21px;
    font-family: "Overpass", sans-serif; font-size: 11.5px;
  }
  .main-nav a { color: var(--white); text-decoration: none; }

  .hero-visual {
    position: absolute; left: 490px; top: 98px; width: 508px; height: 430px;
    background: radial-gradient(circle at 57% 50%, #3ab6e6 0%, #12527f 30%, #06223d 48%, rgba(0,0,0,0) 70%);
  }

  .hero-title {
    position: absolute; left: 84px; top: 193px; width: 430px;
    font-weight: 800; font-size: 31px; line-height: 37.6px; text-transform: uppercase;
  }
  .hero-text {
    position: absolute; left: 87px; top: 316px; width: 390px;
    font-size: 10.5px; line-height: 17.8px;
  }
  .btn-primary {
    position: absolute; left: 88px; top: 437px; width: 120px; height: 35px;
    background: var(--gold); color: var(--ink); font-weight: 700; font-size: 10.5px;
    display: flex; align-items: center; justify-content: center; text-decoration: none;
  }

  .footer-map {
    position: absolute; left: 70px; top: 830px; width: 850px; height: 340px;
    background: radial-gradient(ellipse at center, #161616 0%, #0a0a0a 55%, rgba(0,0,0,0) 75%);
  }

  .facts-card {
    position: absolute; left: 148px; top: 553px; width: 701px; height: 305px;
    background: var(--gold); border-radius: 6px; color: var(--ink);
  }
  .facts-title {
    position: absolute; left: 0; top: 46px; width: 100%; text-align: center;
    font-weight: 800; font-size: 23.5px; line-height: 33px; text-transform: uppercase;
  }
  .facts-list {
    position: absolute; left: 112px; top: 170px; width: 500px;
    display: grid; grid-template-columns: 241px 1fr; row-gap: 9px;
    list-style: none; font-weight: 700; font-size: 14px; line-height: 20px; text-transform: uppercase;
  }

  .site-footer .brand { position: absolute; left: 369px; top: 940px; font-size: 28px; }
  .site-footer .brand-mark { width: 30px; height: 30px; }
  .footer-nav {
    position: absolute; top: 1011px; left: 0; width: 998px;
    display: flex; justify-content: center; gap: 24px;
    font-family: "Overpass", sans-serif; font-size: 12.8px;
  }
  .footer-nav a { color: var(--white); text-decoration: none; }
  .copyright {
    position: absolute; top: 1056px; width: 998px; text-align: center;
    font-family: "Overpass", sans-serif; font-size: 12.8px;
  }
  .social {
    position: absolute; top: 1102px; left: 435px; display: flex; gap: 7px; list-style: none;
  }
  .social li {
    width: 27px; height: 27px; border-radius: 50%; background: var(--muted);
    display: flex; align-items: center; justify-content: center;
  }
  .social li.is-active { background: var(--gold); }
</style>
</head>
<body>
  <div class="promo-bar">Affordable IT Solutions That Revolutionize Tomorrow‘s Air Cargo Today</div>

  <header class="site-header">
    <a class="brand" href="https://www.brisklane.cz/"><span class="brand-mark"></span>Brisklane</a>
    <nav class="main-nav">
      <a href="#">Industries</a><a href="#">Solutions</a><a href="#">Operational Support</a>
      <a href="#">Case Studies</a><a href="#">Testimonials</a><a href="#">News</a><a href="#">About Us</a>
    </nav>
  </header>

  <main>
    <div class="hero-visual" role="img" aria-label="Glowing globe with connected network lines, location pins and an airplane in flight"></div>
    <h1 class="hero-title">Seamlessly connecting the air cargo industry from Manila to Tahiti</h1>
    <p class="hero-text">Blending decades of air cargo knowledge with end-to-end IT solutions. Whether you are an Airline, GSA, GHA, Forwarder or E-commerce Operator, our expertise can elevate your daily workflows, cutting down on expenses, time, and errors. sed do eiusmod tempor incididunt ut labore et dolore magna aliqua. Quis ipsum suspendisse ultrices gravida. Risus commodo viverra maecenas accumsan lacus vel facilisis.</p>
    <a class="btn-primary" href="#">LEARN MORE</a>

    <div class="footer-map" role="img" aria-label="Faint dotted world map background"></div>

    <section class="facts-card">
      <h2 class="facts-title">We are not IT tech experts attempting<br>to do cargo! We are cargo experts<br>with programming skills!</h2>
      <ul class="facts-list">
        <li>Established: 2014</li><li>Countries covered: 18</li>
        <li>Employees: 22</li><li>Connected clients: 20+</li>
        <li>Nr. of annual electronic exchanges:&nbsp; 11,500,000 +</li><li>Nr. of annual AWBs: 350,000 +</li>
      </ul>
    </section>
  </main>

  <footer class="site-footer">
    <a class="brand" href="https://www.brisklane.cz/"><span class="brand-mark"></span>Brisklane</a>
    <nav class="footer-nav">
      <a href="#">Industries</a><a href="#">Solutions</a><a href="#">Operational Support</a>
      <a href="#">Case Studies</a><a href="#">Testimonials</a><a href="#">News</a><a href="#">About Us</a>
    </nav>
    <p class="copyright">©Copyrights 2024&nbsp; Brisklane &nbsp;|&nbsp;&nbsp; All Rights Reserved</p>
    <ul class="social">
      <li class="is-active" aria-label="Social link"></li>
      <li aria-label="Email">
        <svg width="13" height="10" viewBox="0 0 13 10"><rect x="0.5" y="0.5" width="12" height="9" rx="1" fill="#fec820"/><path d="M1 1.5 L6.5 5.5 L12 1.5" stroke="#1a1a1a" stroke-width="1.2" fill="none"/></svg>
      </li>
      <li aria-label="Social link"></li>
      <li aria-label="Social link"></li>
    </ul>
  </footer>
</body>
</html>
```